RWT Fittings Ltd Business Cards

We need a business card with our business logo. We provide window and door installations on high-rises in west coast British Colombia, Canada.

I would like my business information and details on one side of the card, and the other side the company name with logo

Target Market(s)

General Contractors

Industry/Entity Type

Construction

Contact Information for Business Card

one side i want my company name and logo in the dark theme logo that i provided

Requirements
Must have
• Marco Peltieri, 16045518293, RWTFittings@mailbox-demo.com, 1407-5194 Linden Row Burnaby BC, V5H 2K9, Owner & Manager

```html
<!DOCTYPE html>
<html lang="en">
<head>
<meta charset="utf-8">
<title>RWT Fittings Ltd — Business Card</title>
<link rel="stylesheet" href="https://fonts.googleapis.com/css2?family=Open+Sans:wght@400;600;700&display=swap">
<style>
  :root {
    --backdrop: #474747;
    --card: #161616;
    --accent: #29a8e0;
    --ink: #ffffff;
    --emboss: #242424;
    --emboss-edge: #2e2e2e;
  }
  * { margin: 0; padding: 0; box-sizing: border-box; }
  html, body {
    width: 1200px; height: 801px; overflow: hidden;
    background: var(--backdrop);
    font-family: "Open Sans", Arial, sans-serif;
  }
  .canvas {
    width: 1200px; height: 801px;
    display: flex; flex-direction: column; align-items: center; justify-content: center;
    gap: 28px;
  }
  .card {
    position: relative;
    width: 640px; height: 366px;
    background: var(--card);
    overflow: hidden;
    box-shadow: 0 10px 24px rgba(0,0,0,.35);
  }

  /* Front side */
  .brand {
    position: absolute; right: 48px; top: 46px;
    display: flex; align-items: center; gap: 14px;
  }
  .brand-mark { width: 34px; height: 34px; background: var(--accent); }
  .brand-name {
    color: var(--accent); font-weight: 700; font-size: 34px;
    letter-spacing: 3px; text-transform: uppercase; line-height: 1;
    white-space: nowrap;
  }
  .divider {
    position: absolute; left: 285px; right: 28px; top: 186px;
    height: 1px; background: var(--accent);
  }
  .side-tab {
    position: absolute; left: 0; top: 204px;
    width: 22px; height: 44px; background: var(--accent);
  }
  .person { position: absolute; left: 40px; top: 170px; }
  .person-name {
    color: var(--accent); font-weight: 700; font-size: 24px;
    text-transform: uppercase; letter-spacing: .5px; line-height: 1.1;
    white-space: nowrap;
  }
  .person-title { color: var(--ink); font-size: 16px; line-height: 1.3; }
  .contacts {
    position: absolute; left: 40px; top: 262px;
    list-style: none; color: var(--ink); font-size: 15px; line-height: 1.55;
  }
  .contacts li { display: flex; align-items: center; gap: 10px; white-space: nowrap; }
  .contacts svg { width: 13px; height: 13px; flex: none; }
  .address {
    position: absolute; right: 34px; top: 206px;
    color: var(--ink); font-size: 15px; line-height: 1.4; text-align: right;
  }

  /* Back side */
  .card-back { display: flex; align-items: center; justify-content: center; }
  .back-brand { display: flex; align-items: center; gap: 20px; }
  .back-mark {
    width: 58px; height: 58px; background: var(--emboss); flex: none;
  }
  .back-name {
    color: var(--emboss-edge); font-weight: 700; font-size: 40px;
    letter-spacing: 4px; text-transform: uppercase; line-height: 1;
    white-space: nowrap;
  }
</style>
</head>
<body>
<main class="canvas">
  <section class="card card-front" aria-label="Business card front">
    <div class="brand">
      <span class="brand-mark"></span>
      <span class="brand-name">RWT Fittings Ltd</span>
    </div>
    <div class="divider"></div>
    <div class="side-tab"></div>
    <div class="person">
      <p class="person-name">Marco Peltieri</p>
      <p class="person-title">Owner &amp; Manager</p>
    </div>
    <ul class="contacts">
      <li>
        <svg viewBox="0 0 14 14" aria-hidden="true"><path fill="var(--accent)" d="M3 1l2.2 2.6-1.1 1.6c.8 1.7 2 2.9 3.7 3.7l1.6-1.1L12 10l-1.2 2.4C6 12 2 8 1.6 3.2z"/></svg>
        <span>16045518293</span>
      </li>
      <li>
        <svg viewBox="0 0 14 14" aria-hidden="true"><rect x="1" y="3" width="12" height="8" fill="var(--accent)"/><path d="M1 3l6 4.5L13 3" fill="none" stroke="var(--card)" stroke-width="1.2"/></svg>
        <span>RWTFittings@mailbox-demo.com</span>
      </li>
      <li>
        <svg viewBox="0 0 14 14" aria-hidden="true"><circle cx="7" cy="7" r="6" fill="var(--accent)"/><path d="M1 7h12M7 1c-2.5 3-2.5 9 0 12M7 1c2.5 3 2.5 9 0 12" fill="none" stroke="var(--card)" stroke-width="1"/></svg>
        <span>www.rwtfittings-demo.com</span>
      </li>
    </ul>
    <p class="address">1407-5194 Linden Row<br>Burnaby BC, V5H 2K9</p>
  </section>

  <section class="card card-back" aria-label="Business card back">
    <div class="back-brand">
      <span class="back-mark"></span>
      <span class="back-name">RWT Fittings Ltd</span>
    </div>
  </section>
</main>
</body>
</html>
```